Launching a new real estate agency in Monaco

Hello, I am opening a new real estate agency in Monaco. For the purpose of my activity, in order to be known quickly among a fierce competition I need an advertising campaign that will be broadcast in local magazines, newspapers, paper board, etc.

You will find example of pictures of Monaco on which I have the rights and my logo. You can always pick other images that I can buy if the price is reasonable for a commercial use (<200 $)

Please respect the color code.

I wish you good luck and look forward to give you my feedbacks

Reason: Only few projects posted were respecting the brief and of quality. Hoping to receive more in coming days

Target Market(s)

International high-end clientele of all ages, all genders.

Industry/Entity Type

Real Estate Agent

Font styles to use
Serif

Requirements
Must have
• 1/ My logo
• 2/ This message "Un nouveau regard sur l'immobilier" means in English a fresh look at real estate or new eyes on real-estate.
• 3/ My address: 14 rue des Ormeaux, Galerie Bellerive Nord, 98 000 Monaco
• 4/ Phone number: +377.93.48.25.07
• 5/ Website: www.corvano-immo.com.
• 6/ Format: Files should be easily adjustable but I'd like a vertical display to fit easily in Magazines, Poster and billboard. So please work in high resolution !
Nice to have
• Please think about your design in accordance with the message I want to display.
Should not have
• A simple poster with a picture of Monaco that does not take into consideration the message of the advertisement, "Un nouveau regard sur l'immobilier" which means in english, new eyes on real-estate or a new look at real-estate, or new vision at real-estate.

```html
<!DOCTYPE html>
<html lang="fr">
<head>
<meta charset="utf-8">
<title>Corvano Immo — Un nouveau regard sur l'immobilier</title>
<link rel="stylesheet" href="https://fonts.googleapis.com/css2?family=Crimson+Pro:wght@400;600&display=swap">
<style>
  :root {
    --sea-deep: #0b55c2;
    --sea-bright: #1a74dc;
    --harbour: #3d8fd6;
    --roof: #c98a63;
    --stone: #d9c3a8;
    --garden: #4f7a3a;
    --paper: #ffffff;
    --ink: #262626;
    --ink-soft: #3a3a3a;
  }
  * { margin: 0; padding: 0; box-sizing: border-box; }
  html, body { width: 927px; height: 1200px; overflow: hidden; background: var(--paper); }
  .poster {
    position: relative;
    width: 927px;
    height: 1200px;
    overflow: hidden;
    background: var(--paper);
    font-family: "Crimson Pro", Georgia, serif;
  }
  .poster__art { position: absolute; inset: 0; width: 927px; height: 1200px; }
  .brand {
    position: absolute;
    left: 48px;
    top: 70px;
    display: flex;
    align-items: center;
    gap: 16px;
    color: var(--paper);
    font-weight: 600;
    font-size: 46px;
    letter-spacing: 4px;
  }
  .brand__mark { width: 18px; height: 18px; background: var(--paper); }
  .tagline {
    position: absolute;
    left: 419px;
    top: 706px;
    transform: translate(-50%, -50%) rotate(-56deg);
    white-space: nowrap;
    font-size: 35px;
    color: var(--ink);
  }
  .contact {
    position: absolute;
    color: var(--ink-soft);
    font-size: 23px;
    display: flex;
    align-items: center;
    gap: 8px;
    white-space: nowrap;
  }
  .contact svg { width: 24px; height: 24px; flex: none; }
  .contact--phone-web { left: 243px; top: 1085px; gap: 8px; }
  .contact--phone-web .sep { width: 10px; }
  .contact--address { right: 10px; top: 1126px; gap: 5px; }
</style>
</head>
<body>
<main class="poster">
  <svg class="poster__art" viewBox="0 0 840 1086" preserveAspectRatio="none" aria-hidden="false">
    <defs>
      <linearGradient id="monaco-tones" x1="0" y1="0" x2="0.35" y2="1">
        <stop offset="0" stop-color="var(--sea-deep)"/>
        <stop offset="0.35" stop-color="var(--sea-bright)"/>
        <stop offset="0.55" stop-color="var(--harbour)"/>
        <stop offset="0.7" stop-color="var(--stone)"/>
        <stop offset="0.85" stop-color="var(--roof)"/>
        <stop offset="1" stop-color="var(--garden)"/>
      </linearGradient>
    </defs>
    <rect class="photo" role="img" aria-label="Vue aérienne de Monaco : port de plaisance avec yachts, mer bleue et Rocher aux toits orangés"
          x="0" y="0" width="840" height="1086" fill="url(#monaco-tones)"/>
    <polygon class="frame-chevron" points="745,0 840,0 840,390 652,137" fill="var(--paper)"/>
    <polygon class="frame-band" points="527,320 625,460 310,928 840,928 840,1086 12,1086" fill="var(--paper)"/>
  </svg>

  <div class="brand"><span class="brand__mark"></span>CORVANO IMMO</div>

  <p class="tagline">Un nouveau regard sur l'immobilier</p>

  <p class="contact contact--phone-web">
    <svg viewBox="0 0 24 24" fill="none" stroke="currentColor" stroke-width="1.6"><circle cx="12" cy="12" r="10"/><path d="M9 7.5c-.8.5-1.2 1.5-.8 2.7.8 2.3 2.5 4.3 4.5 5.3 1 .5 2.1.2 2.7-.6l-1.6-1.6-1.3.6c-1-.6-1.9-1.6-2.4-2.7l.8-1.2z" fill="currentColor" stroke="none"/></svg>
    <span>+377.93.48.25.07</span>
    <span class="sep"></span>
    <svg viewBox="0 0 24 24" fill="none" stroke="currentColor" stroke-width="1.3"><circle cx="12" cy="12" r="10"/><ellipse cx="12" cy="12" rx="4.5" ry="10"/><path d="M2 12h20M3.5 7h17M3.5 17h17"/></svg>
    <span>www.corvano-immo.com.</span>
  </p>

  <p class="contact contact--address">
    <svg viewBox="0 0 24 24"><path d="M12 2a7 7 0 0 0-7 7c0 5 7 13 7 13s7-8 7-13a7 7 0 0 0-7-7zm0 9.5a2.5 2.5 0 1 1 0-5 2.5 2.5 0 0 1 0 5z" fill="currentColor"/></svg>
    <span>14 rue des Ormeaux, Galerie Bellerive Nord, 98 000 Monaco</span>
  </p>
</main>
</body>
</html>
```